Veltrano.co - Polar Expeditions Specialists

We need a modern, visually striking business card for Veltrano.co, a company specialized in selling expedition cruises to the most remote regions on Earth, with a focus on the Arctic and Antarctica. The design should instantly communicate that the cardholder is an expert in polar travel. Use clean, premium aesthetics with cool tones like icy blue and white, possibly incorporating polar imagery (ice, glaciers, penguins, etc.)

Attached the logo

Contact Information for Business Card

Feels high-end and trustworthy.. Visually memorable — encourages people to keep it

Colors
0054AA
0677BA
7BADD7
CADEEF
E8F1F8

Requirements
Must have
• ice, glaciers, penguins, montains
Nice to have
• modern, transparente,

```html
<!DOCTYPE html>
<html lang="en">
<head>
<meta charset="utf-8">
<title>Veltrano.co – Business Card</title>
<link href="https://fonts.googleapis.com/css2?family=Poppins:wght@400;500;600;700&display=swap" rel="stylesheet">
<style>
  :root {
    --page: #e3e7e8;
    --card: #1f2024;
    --blue: #2b78c0;
    --white: #ffffff;
    --pattern-dark: #0e0f11;
    --pattern-mid: #2a2b30;
    --pattern-light: #55575d;
  }
  * { margin: 0; padding: 0; box-sizing: border-box; }
  html, body { width: 1200px; height: 960px; overflow: hidden; }
  body {
    background: var(--page);
    font-family: "Poppins", sans-serif;
    position: relative;
  }
  .card {
    position: absolute;
    left: 252px;
    width: 700px;
    height: 398px;
    border-radius: 28px;
    background: var(--card);
    overflow: hidden;
    box-shadow: -4px 4px 0 var(--blue), 0 18px 30px rgba(0,0,0,0.28);
  }
  .card--front { top: 60px; }
  .card--back { top: 500px; }

  /* front */
  .front-pattern {
    position: absolute;
    inset: 0;
    background:
      radial-gradient(ellipse 70% 80% at 100% 0%, rgba(120,122,128,0.45), transparent 70%),
      linear-gradient(225deg, var(--pattern-light) 0%, var(--pattern-mid) 48%, var(--pattern-dark) 100%);
  }
  .front-brand {
    position: absolute;
    left: 520px;
    top: 278px;
    width: 130px;
    text-align: center;
    color: var(--blue);
  }
  .front-brand__mark {
    width: 30px;
    height: 30px;
    border-radius: 50%;
    background: var(--blue);
    margin: 0 auto 4px;
  }
  .front-brand__name { font-size: 17px; font-weight: 700; line-height: 1.1; }
  .front-brand__tag { font-size: 6px; font-weight: 600; margin-top: 2px; }

  /* back */
  .brand {
    position: absolute;
    left: 30px;
    top: 108px;
    width: 290px;
    text-align: center;
    color: var(--blue);
  }
  .brand__mark {
    width: 84px;
    height: 84px;
    border-radius: 50%;
    background: var(--blue);
    margin: 0 auto 20px;
  }
  .brand__name { font-size: 50px; font-weight: 700; line-height: 1; letter-spacing: -0.5px; }
  .brand__tag { font-size: 15px; font-weight: 600; margin-top: 8px; }

  .divider {
    position: absolute;
    left: 348px;
    top: 69px;
    width: 1px;
    height: 239px;
    background: var(--blue);
    opacity: 0.8;
  }

  .person {
    position: absolute;
    left: 404px;
    top: 110px;
  }
  .person__name { font-size: 37px; color: var(--blue); line-height: 1.1; white-space: nowrap; }
  .person__first { font-weight: 600; }
  .person__last { font-weight: 400; }
  .person__title { font-size: 19px; font-weight: 500; color: var(--white); margin-top: 0; }

  .contacts {
    position: absolute;
    left: 404px;
    top: 199px;
    list-style: none;
  }
  .contacts li {
    display: flex;
    align-items: center;
    gap: 12px;
    height: 26px;
    font-size: 20px;
    color: var(--white);
  }
  .contacts svg { width: 17px; height: 17px; flex: none; }

  .address-band {
    position: absolute;
    left: 0;
    right: 0;
    top: 344px;
    height: 30px;
    background: var(--blue);
    color: var(--white);
    font-size: 19px;
    font-weight: 500;
    line-height: 31px;
    padding-left: 61px;
  }
  .band-mark {
    position: absolute;
    left: 604px;
    top: 330px;
    width: 58px;
    height: 58px;
    border-radius: 50%;
    background: var(--blue);
  }
</style>
</head>
<body>

  <section class="card card--front">
    <div class="front-pattern" role="img" aria-label="Repeating grid of tone-on-tone polar emblem pattern fading from black to grey"></div>
    <div class="front-brand">
      <div class="front-brand__mark"></div>
      <div class="front-brand__name">Veltrano.co</div>
      <div class="front-brand__tag">Polar Expeditions Specialists</div>
    </div>
  </section>

  <section class="card card--back">
    <div class="brand">
      <div class="brand__mark"></div>
      <div class="brand__name">Veltrano.co</div>
      <div class="brand__tag">Polar Expeditions Specialists</div>
    </div>

    <div class="divider"></div>

    <div class="person">
      <div class="person__name"><span class="person__first">Lenka</span> <span class="person__last">Marova</span></div>
      <div class="person__title">Founder &amp; CEO</div>
    </div>

    <ul class="contacts">
      <li>
        <svg viewBox="0 0 24 24" aria-hidden="true"><path fill="#2b78c0" d="M6.6 10.8a15.1 15.1 0 0 0 6.6 6.6l2.2-2.2a1 1 0 0 1 1-.25 11.4 11.4 0 0 0 3.6.57 1 1 0 0 1 1 1V20a1 1 0 0 1-1 1A17 17 0 0 1 3 4a1 1 0 0 1 1-1h3.5a1 1 0 0 1 1 1c0 1.25.2 2.45.57 3.57a1 1 0 0 1-.25 1z"/></svg>
        <span>(512) 604-1837</span>
      </li>
      <li>
        <svg viewBox="0 0 24 24" aria-hidden="true"><circle cx="12" cy="12" r="9" fill="none" stroke="#2b78c0" stroke-width="2"/><path d="M3 12h18M12 3c3 3 3 15 0 18M12 3c-3 3-3 15 0 18" fill="none" stroke="#2b78c0" stroke-width="1.6"/></svg>
        <span>info@yourwebsite.com</span>
      </li>
      <li>
        <svg viewBox="0 0 24 24" aria-hidden="true"><rect x="2.5" y="6" width="19" height="13" rx="1.5" fill="none" stroke="#2b78c0" stroke-width="2"/><path d="M3 7l9 7 9-7" fill="none" stroke="#2b78c0" stroke-width="2"/></svg>
        <span>www.yourwebsite.com</span>
      </li>
    </ul>

    <div class="address-band">418 Harbor Line Ave. Suite 310 Portland, ME 04101</div>
    <div class="band-mark"></div>
  </section>

</body>
</html>
```